lofty birch website

We need a new website for our new business division. We are a sustainable design firm specializing in servicing the needs if architects and developers. We have a staff consisting of architects, engineers, and former contractors and we understand green must make sense.

Bottomline - the only sustainable and lofty birch solutions are those thatbare good for the environment and good for our clients bottom line.

Our company is lofty birch and we will send you a copy of our logo you will see our tagline. Is simple. sustainable. solutions. The play with the periods is that we believe their are simple sustainable solutions and we want to use the words together and possible let each stand alone to accentuate their individual meaning in regards to benefit to our clients.

We want a cool splash page with nich graphics and pictures then later pages to feature projects and design ideas.

Target Market(s)

Our target customers are architects, developers, and contractors who would need assistance with the design process for a VARO project or assisatnce with a building owner who wants to make tehir facilty more environmentally friendly and save energy costs at the same tiem.

Industry/Entity Type

Environment

Requirements
Must have
• Needs a construction look with an environmentally friendly surrounding that is pleasing to look at. Must appeal to the client not only as environmentally friendly but also a wise investment.
Nice to have
• Opportunity for a connection to Social networking including a blog.
Should not have
• A totally environmental building feel at whatever cost. We want to emphasize that it is possible to build environmental friendly and save you money over the life of your building

```html
<!DOCTYPE html>
<html lang="en">
<head>
<meta charset="utf-8">
<title>lofty birch — simple. sustainable. solutions.</title>
<link rel="stylesheet" href="https://fonts.googleapis.com/css2?family=Arimo:wght@400;700&display=swap">
<style>
:root{
  --leaf-light:#c9dc5a;
  --leaf-mid:#8fb52a;
  --leaf-dark:#4f7a17;
  --brand-green:#5aa02c;
  --accent-green:#6fbf3a;
  --ink:#5f6062;
  --body-text:#8a8b8d;
  --nav-black:#1c1c1c;
  --footer-top:#3a3a3a;
  --footer-bottom:#141414;
  --white:#ffffff;
  --rule:#c9c9c9;
  --photo-dark:#2e3033;
  --photo-mid:#6b6e72;
  --dot:#c7d21a;
  --dot-active:#3b9a2c;
}
*{box-sizing:border-box;margin:0;padding:0}
html,body{width:1200px;height:1159px;overflow:hidden;background:var(--white)}
body{font-family:"Arimo",Arial,sans-serif;position:relative}
.canvas{position:absolute;inset:0;border:1px solid #9a9a9a;overflow:hidden}

.leaf-backdrop{position:absolute;left:0;top:0;width:1200px;height:560px;
  background:
    linear-gradient(180deg,rgba(255,255,255,0) 60%,var(--white) 100%),
    radial-gradient(ellipse at 15% 30%,var(--leaf-light) 0%,var(--leaf-mid) 55%,var(--leaf-dark) 100%);}

.page-panel{position:absolute;left:152px;top:100px;width:899px;height:770px;background:var(--white);border-radius:0 16px 0 0}
.logo-tab{position:absolute;left:152px;top:0;width:318px;height:104px;background:var(--white);border-radius:0 0 40px 0}
.logo{position:absolute;left:176px;top:30px;display:flex;align-items:center;gap:10px}
.logo-mark{width:42px;height:42px;background:var(--brand-green)}
.logo-name{font-size:33px;color:var(--ink);font-weight:400;letter-spacing:-.5px;line-height:1}
.logo-tagline{position:absolute;left:240px;top:70px;font-size:13px;color:var(--ink)}

.main-nav{position:absolute;left:496px;top:26px;width:553px;height:51px;background:linear-gradient(#2c2c2c,var(--nav-black));border-radius:8px;display:flex}
.main-nav a{flex:1;display:flex;align-items:center;justify-content:center;color:var(--white);font-weight:700;font-size:16px;text-decoration:none;border-right:1px solid #3d3d3d}
.main-nav a:last-child{border-right:none}

.hero-slider{position:absolute;left:172px;top:120px;width:857px;height:397px;
  background:linear-gradient(90deg,var(--photo-mid) 0%,var(--photo-dark) 40%,#1a1b1d 70%,#8fa2b5 100%)}
.slider-arrow{position:absolute;top:303px}
.slider-arrow.prev{left:193px}
.slider-arrow.next{left:943px}
.slider-dots{position:absolute;left:193px;top:485px;display:flex;gap:6px}
.slider-dots span{width:20px;height:20px;border-radius:50%;background:var(--dot)}
.slider-dots span.active{background:var(--dot-active)}

.feature{position:absolute;top:552px}
.feature h2{font-size:36px;color:var(--ink);font-weight:700;text-align:center;margin-bottom:12px}
.feature p{font-size:13.5px;line-height:17px;color:var(--body-text)}
.feature-simple{left:172px;width:272px}
.feature-sustainable{left:475px;width:240px}
.feature-sustainable h2{text-align:left}
.feature-solution{left:761px;width:236px}
.benefit-list{list-style:none}
.benefit-list li{font-size:13.5px;color:var(--body-text);height:22.5px;display:flex;align-items:center;gap:8px}
.benefit-list li::before{content:"";width:0;height:0;border-left:9px solid var(--brand-green);border-top:4px solid transparent;border-bottom:4px solid transparent}
.column-rule{position:absolute;top:555px;width:2px;height:275px;background:var(--rule)}

.read-more{position:absolute;top:826px;width:133px;height:32px;background:linear-gradient(#333,#0f0f0f);border-radius:7px;color:var(--white);font-weight:700;font-size:14px;display:flex;align-items:center;justify-content:center}

.site-footer{position:absolute;left:0;top:867px;width:1200px;height:292px;background:linear-gradient(var(--footer-top),var(--footer-bottom))}
.footer-heading{position:absolute;top:891px;font-size:16px;font-weight:700;color:var(--accent-green)}
.footer-list{position:absolute;top:936px;list-style:none}
.footer-list li{height:25.7px;display:flex;align-items:center;padding-left:20px;font-size:12px;color:var(--white);border-bottom:1.5px dashed #d8d8d8}
.footer-menu{left:152px;width:278px}
.footer-partners{left:460px;width:279px}
.footer-partners li{font-weight:700;padding-left:20px}
.social-links{position:absolute;left:888px;top:903px;display:flex;gap:5px}
.social-links span{width:32px;height:32px;border-radius:4px}
.contact-form label{position:absolute;left:790px;font-size:11px;font-weight:700;color:var(--accent-green)}
.contact-form .field{position:absolute;left:790px;width:239px;background:var(--white)}
.submit-button{position:absolute;left:946px;top:1104px;width:85px;height:20px;border-radius:4px;background:linear-gradient(#8bd64f,#55a82a);color:#111;font-size:12px;font-weight:700;display:flex;align-items:center;justify-content:center}
</style>
</head>
<body>
<div class="canvas">
  <div class="leaf-backdrop" role="img" aria-label="Close-up of a bright green leaf with veins"></div>
  <div class="page-panel"></div>
  <div class="logo-tab"></div>

  <div class="logo"><span class="logo-mark"></span><span class="logo-name">lofty birch</span></div>
  <div class="logo-tagline">simple. sustainable. solutions.</div>

  <nav class="main-nav">
    <a>Home</a><a>About Us</a><a>Services</a><a>Work</a><a>Contact</a>
  </nav>

  <div class="hero-slider" role="img" aria-label="Modern grey concrete house with a small tree in a gravel courtyard"></div>
  <svg class="slider-arrow prev" width="68" height="68" viewBox="0 0 68 68">
    <circle cx="34" cy="34" r="33" fill="#8a8a8a" fill-opacity=".8"/>
    <polygon points="14,34 48,20 40,34 48,48" fill="#222"/>
  </svg>
  <svg class="slider-arrow next" width="68" height="68" viewBox="0 0 68 68">
    <circle cx="34" cy="34" r="33" fill="#8a8a8a" fill-opacity=".8"/>
    <polygon points="54,34 20,20 28,34 20,48" fill="#222"/>
  </svg>
  <div class="slider-dots"><span class="active"></span><span></span><span></span><span></span><span></span></div>

  <section class="feature feature-simple">
    <h2>Simple</h2>
    <ul class="benefit-list">
      <li>It is a long established fact that a reader</li>
      <li>It is a long established fact that a reader</li>
      <li>It is a long established fact that a reader</li>
      <li>It is a long established fact that a reader</li>
      <li>It is a long established fact that a reader</li>
      <li>It is a long established fact that a reader</li>
      <li>It is a long established fact that a reader</li>
      <li>It is a long established fact that a reader</li>
    </ul>
  </section>
  <div class="column-rule" style="left:456px"></div>
  <section class="feature feature-sustainable">
    <h2>Sustainable</h2>
    <p>Lorem Ipsum is simply dummy text of the printing and typesetting industry.Lorem Ipsum has been the industry's standard dummy text ever since the 1500s, when an unknown printer took a galley of type and scrambled it to make a type specimen book. It has survived not only five centuries, but also the leap into electronic typesetting, remaining essentially unchanged. It was popularised in the</p>
  </section>
  <div class="column-rule" style="left:741px"></div>
  <section class="feature feature-solution">
    <h2>Solution</h2>
    <p>Lorem Ipsum is simply dummy text of the printing and typesetting industry.Lorem Ipsum has been the industry's standard dummy text ever since the 1500s, when an unknown printer took a galley of type and scrambled it to make a type specimen book. It has survived not only five centuries, but also the leap into electronic typesetting, remaining essentially unchanged.</p>
  </section>

  <a class="read-more" style="left:308px">Read More »</a>
  <a class="read-more" style="left:593px">Read More »</a>
  <a class="read-more" style="left:901px">Read More »</a>

  <footer class="site-footer"></footer>
  <div class="footer-heading" style="left:170px">Menu:</div>
  <ul class="footer-list footer-menu">
    <li>Home</li><li>About Us</li><li>Services</li><li>Work</li><li>Gallery</li><li>Blog</li><li>Contact</li>
  </ul>
  <div class="footer-heading" style="left:478px">Partners:</div>
  <ul class="footer-list footer-partners">
    <li>Contrary to popular belief</li><li>Contrary to popular belief</li><li>Contrary to popular belief</li><li>Contrary to popular belief</li><li>Contrary to popular belief</li><li>Contrary to popular belief</li><li>Contrary to popular belief</li>
  </ul>
  <div class="footer-heading" style="left:784px">Contact Us:</div>
  <div class="social-links">
    <span style="background:#4a6ea9"></span><span style="background:#4fb8dc"></span><span style="background:#f08a24"></span><span style="background:#f26522"></span>
  </div>
  <form class="contact-form">
    <label style="top:946px">Name:</label>
    <div class="field" style="top:962px;height:16px"></div>
    <label style="top:980px">Email:</label>
    <div class="field" style="top:993px;height:16px"></div>
    <label style="top:1011px">Coments:</label>
    <div class="field" style="top:1025px;height:71px"></div>
    <div class="submit-button">Submit</div>
  </form>
</div>
</body>
</html>
```